Superfoods Nutrition for Elderly

We need a thematic packaging design that fits our elderly nutrition products, that is based on our "3 Ws ethos" - eating Wisely, Widely & Wholly.

Wisely - selected superfoods and ingredients - NZ and other sources
Widely - based on the "rainbow diet" philosophy
Wholly - all natural, (no artificial flavours, colors etc). Formulated as complete meals (NOT supplementation)

Mediums:
- 400-450gram re-sealable doy packs
- 400-450gram re-sealable tin cans

Look n Feel:
Tuarango - https://tuarangokindness.com
Poli Vane - https://www.polvane.co.nz/
Juniper bluff - https://dinegladstaygood.co.nz/collections/cereals

The name of our products may/may not be “vital rori”. Our on-going research tells us that for the Asian market, an icon or character to personify our product may be a sound strategy. This is only for the designer to take note off.

Deliverables:
* 5 packaging designs in the range.
1x yellow + orange colored foods (star ingredient: “bright so” – passion fruit powder)
1x red colored foods (star ingredient: (star ingredient: - Manuka honey )
1x blues/purple colored foods: (star ingredient: lumoka blackcurrant)
1 x green coloured foods (star ingredient: Green kiwi)
1 x brown/white (star ingredients: harrowby’s grass fed bone broth)

brand name, please use “VitalRori” for now.

These will be the products:

Blue/purple: “Instant oatmeal porridge”
Ingredients: Rolled Baby Oats, Blueberries, Blackcurrant Powder, chia seeds, Blue Spirulina, Sheep’s Milk.
Star ingredient: Blackcurrant powder (support eyesight)

Brown/White: “Instant Brown Rice”
Ingredients: Organic Brown Rice, Grass fed bone broth powder, collagen peptide powder, black sesame seeds, onions and garlic powder, dried mushrooms, probiotics.
Star ingredient: Grass fed bone broth (support joint health)

Green: “Instant Smoothie”
Ingredients: Organic Green Kiwifruit, Kale powder, green apple powder, whey protein concentrate, probiotics, and sheep’s milk powder
Star ingredient: Organic green kiwi fruit(supports immunity)

Yellow/Orange “Instant Oatmeal”
Ingredients: Organic rolled baby oats, banana, organic passionfruit, apricot, dried mango, probiotics, cinnamon, sheep’s milk powder.
Star ingredient: Organic passionfruit(regulates blood glucose)

Red: “ instant amaranth cereal”
Ingredients: Organic amaranth, red apples, pomegranate, cranberries, Manuka honey powder, probiotics, sheep’s milk
Star ingredient: Manuka honey powder (anti-inflammatory)

Target Market(s)

Whose attention we are trying to grab?

Primary:
- 20 to 40 year olds buying these products for their parents/grand parents
- Health Nutrition conscious “golden agers”
Secondary
- Professional Caregivers to the elderly (homes, private hospitals etc)
- 40 year olds in the “prevention” mind set.

Font styles to use
Serif
Sans Serif

Colors

Designer to choose colors to be used in the design.

Requirements
Must have
• Mandatory:
• - clear visual que of the food color/s
• - "New Zealand" origin must come through strongly.
• - must have a blurp or feature of the star ingredient for each with mention of brand.
• e.g. for the blues+ purple, NZ blackcurrant powder for improved eyesight (cataract prevention).
• - icons for “heart health, “eyesight”, “mobility”, “gut-health”.
• - every other ingredient must be stated.
• The name of product may/may not be “vitalrori”. Our on-going research tells us that for the Asian market, an icon or character to personify our product may be a sound strategy. This is only for the designer to take note off.
Nice to have
• Desirables:
• Ingredient origin story - e.g blackcurrant comes from Timaru etc.
• (refer to Pemberlys destination marketing…)

```html
<!DOCTYPE html>
<html lang="en">
<head>
<meta charset="utf-8">
<title>VitalRori Instant Brown Rice – Tin Label</title>
<link rel="stylesheet" href="https://fonts.googleapis.com/css2?family=Baloo+2:wght@500;600;700&family=Comfortaa:wght@500&display=swap">
<style>
  :root {
    --page-bg: #eeeeee;
    --label-bg: #f7f7f7;
    --ink-dark: #3a3a3a;
    --brown: #4b2410;
    --brown-mid: #6b3a1f;
    --rule: #b59a86;
    --icon-grey: #a9a9a9;
    --icon-text: #9a9a9a;
    --photo-cream: #ece4d4;
    --photo-oat: #d8c4a0;
    --photo-tan: #b98f5c;
    --photo-edge: #9c7445;
  }
  * { box-sizing: border-box; margin: 0; padding: 0; }
  html, body { width: 1200px; height: 1200px; overflow: hidden; }
  body {
    background: var(--page-bg);
    font-family: "Baloo 2", "Trebuchet MS", sans-serif;
    display: flex; align-items: center; justify-content: center;
  }
  .tin-label {
    width: 620px; height: 1060px;
    background: var(--label-bg);
    display: flex; flex-direction: column; align-items: center;
    padding-top: 112px;
    box-shadow: 0 2px 10px rgba(0,0,0,0.08);
  }
  .brand-name {
    font-weight: 700; font-size: 86px; line-height: 1;
    color: var(--ink-dark); letter-spacing: -1px;
  }
  .rule { width: 380px; height: 1px; background: var(--rule); }
  .rule--top { margin-top: 52px; }
  .product-title {
    font-weight: 600; font-size: 66px; line-height: 1;
    color: var(--brown); margin: 22px 0 14px; letter-spacing: -1px;
  }
  .made-with {
    margin-top: 20px; font-weight: 500; font-size: 19px; color: var(--brown);
  }
  .star-ingredient {
    font-weight: 600; font-size: 32px; line-height: 1.1; color: var(--brown);
  }
  .benefit-pill {
    margin-top: 6px; padding: 0 12px;
    background: var(--brown-mid); color: #fff;
    border-radius: 12px; font-size: 19px; font-weight: 500; line-height: 26px;
  }
  .hero-photo {
    margin-top: 36px; width: 540px; height: 310px;
    border-radius: 155px;
    background: radial-gradient(ellipse at 50% 50%,
      var(--photo-cream) 0%, var(--photo-oat) 42%, var(--photo-tan) 75%, var(--photo-edge) 100%);
  }
  .rule--icons { margin-top: 26px; width: 420px; }
  .benefit-icons {
    display: flex; justify-content: space-between; width: 440px; margin: 10px 0 8px;
  }
  .benefit {
    width: 100px; display: flex; flex-direction: column; align-items: center;
    font-size: 15px; color: var(--icon-text); font-weight: 500;
  }
  .benefit svg { width: 58px; height: 50px; }
  .rule--bottom { width: 420px; }
  .net-weight {
    margin-top: 24px; font-family: "Comfortaa", sans-serif;
    font-size: 19px; color: var(--brown);
  }
</style>
</head>
<body>
  <main class="tin-label">
    <div class="brand-name">VitalRori</div>
    <div class="rule rule--top"></div>
    <h1 class="product-title">Instant Brown Rice</h1>
    <div class="rule"></div>
    <p class="made-with">Made With</p>
    <p class="star-ingredient">Harrowby’s Grass Fed Bone Broth</p>
    <span class="benefit-pill">Supports Joint Health</span>

    <div class="hero-photo" role="img" aria-label="Photo: bowl of creamy brown rice porridge topped with chopped almonds and dried cranberries, flanked by piles of raw brown rice grains"></div>

    <div class="rule rule--icons"></div>
    <div class="benefit-icons">
      <div class="benefit">
        <svg viewBox="0 0 58 50" aria-hidden="true"><path d="M29 46 C10 32 4 24 4 15 C4 8 10 3 17 3 C22 3 26 6 29 10 C32 6 36 3 41 3 C48 3 54 8 54 15 C54 24 48 32 29 46 Z" fill="var(--icon-grey)"/></svg>
        Heart Health
      </div>
      <div class="benefit">
        <svg viewBox="0 0 58 50" aria-hidden="true"><path d="M3 25 C15 9 43 9 55 25 C43 41 15 41 3 25 Z" fill="none" stroke="var(--icon-grey)" stroke-width="4"/><circle cx="29" cy="25" r="10" fill="var(--icon-grey)"/><circle cx="29" cy="25" r="4" fill="var(--label-bg)"/></svg>
        Eyesight
      </div>
      <div class="benefit">
        <svg viewBox="0 0 58 50" aria-hidden="true"><path d="M12 30 A17 17 0 1 1 29 42" fill="none" stroke="var(--icon-grey)" stroke-width="4" stroke-linecap="round"/><path d="M22 36 L29 42 L22 48" fill="none" stroke="var(--icon-grey)" stroke-width="4" stroke-linecap="round" stroke-linejoin="round"/></svg>
        Mobility
      </div>
      <div class="benefit">
        <svg viewBox="0 0 58 50" aria-hidden="true"><path d="M24 3 V14 C24 18 40 16 42 26 C44 38 34 44 26 42 C20 40 20 34 14 36 V47" fill="none" stroke="var(--icon-grey)" stroke-width="3" stroke-linecap="round"/><path d="M34 28 h6 M37 25 v6" stroke="var(--icon-grey)" stroke-width="2"/></svg>
        Gut-Health
      </div>
    </div>
    <div class="rule rule--bottom"></div>
    <p class="net-weight">Net weight: 450g</p>
  </main>
</body>
</html>
```